Unique Business Card Design

Unique Business Card design for our orthotic and prosthetic company. Our logo is on our website, color is light blue. Unique shape (artificial leg shaped, vertical, etc..) preferred. Logo, business name, individual name and basic demographics needed.

Industry/Entity Type

Business

Contact Information for Business Card

Logo, Industry, Phone # Logo, "Prosthetic & Orthotic Services" Place to add individual name and contact info

Colors
cee9f5

Requirements
Must have
• The icon must be there, placement of "Prosthetic & Orthotic Services" can be moved
Nice to have
• Like the mix of light blue, and a little darker blue. One design included the icons from my website which was a nice touch

```html
<!DOCTYPE html>
<html lang="en">
<head>
<meta charset="utf-8">
<title>Kinetra Limb Co. – Business Card</title>
<link rel="stylesheet" href="https://fonts.googleapis.com/css2?family=Open+Sans:wght@600;700&family=Roboto:ital,wght@0,400;0,700;1,400&family=Crimson+Text:ital@1&display=swap">
<style>
  :root {
    --brand-blue: #24649a;
    --brand-blue-deep: #1f5a8c;
    --card-white: #f7f7f7;
    --backdrop: #e4e4e4;
    --ink: #333333;
  }
  * { margin: 0; padding: 0; box-sizing: border-box; }
  html, body { width: 1200px; height: 576px; overflow: hidden; }
  body { background: var(--backdrop); position: relative; font-family: "Roboto", sans-serif; }

  .card { position: absolute; border-radius: 7px; overflow: hidden; }
  .card--front { left: 82px; top: 139px; width: 484px; height: 292px;
    background: linear-gradient(180deg, #26679d 0%, var(--brand-blue-deep) 100%); color: #fff; }
  .card--back { left: 602px; top: 139px; width: 481px; height: 290px; background: var(--card-white); color: var(--ink); }

  .brand-mark { position: absolute; border-radius: 50%; }
  .card--front .brand-mark { left: 92px; top: 107px; width: 78px; height: 78px; background: #fff; }
  .card--back .brand-mark { left: 194px; top: 29px; width: 68px; height: 68px; background: var(--brand-blue); }

  .brand-name { position: absolute; font-family: "Open Sans", sans-serif; font-weight: 600; white-space: nowrap; letter-spacing: 0.2px; }
  .card--front .brand-name { left: 190px; top: 104px; font-size: 23px; }
  .card--back .brand-name { left: 280px; top: 32px; font-size: 19px; color: var(--brand-blue); }

  .brand-rule { position: absolute; height: 2px; }
  .card--front .brand-rule { left: 190px; top: 138px; width: 202px; background: #fff; }
  .card--back .brand-rule { left: 280px; top: 64px; width: 176px; background: var(--brand-blue); }

  .tagline { position: absolute; font-family: "Crimson Text", serif; font-style: italic; white-space: nowrap; }
  .card--front .tagline { left: 202px; top: 141px; font-size: 14.5px; }
  .card--back .tagline { left: 290px; top: 66px; font-size: 12px; color: var(--brand-blue); }

  .main-phone { position: absolute; left: 213px; top: 155px; font-family: "Open Sans", sans-serif;
    font-weight: 700; font-size: 21px; letter-spacing: 1.5px; }

  .person-name { position: absolute; left: 25px; top: 136px; font-size: 20px; font-weight: 700; color: var(--brand-blue); }
  .person-title { position: absolute; left: 25px; top: 162px; font-size: 11px; font-style: italic; }

  .contact-list { position: absolute; list-style: none; font-size: 13px; }
  .contact-list li { display: flex; align-items: center; height: 17px; white-space: nowrap; }
  .contact-list svg { width: 12px; height: 12px; margin-right: 8px; fill: var(--brand-blue); flex: none; }
  .contact-list--personal { left: 25px; top: 224px; }
  .contact-list--office { left: 254px; top: 187px; }
  .contact-list--office li { height: 17px; }
  .contact-list .address { margin-left: -6px; margin-top: 4px; }

  .footer-band { position: absolute; left: 0; bottom: 0; width: 100%; height: 17px; background: var(--brand-blue); }
</style>
</head>
<body>

<section class="card card--front">
  <span class="brand-mark"></span>
  <div class="brand-name">KINETRA LIMB CO.</div>
  <div class="brand-rule"></div>
  <div class="tagline">Prosthetic &amp; Orthotic Services</div>
  <div class="main-phone">718.555.0142</div>
</section>

<section class="card card--back">
  <span class="brand-mark"></span>
  <div class="brand-name">KINETRA LIMB CO.</div>
  <div class="brand-rule"></div>
  <div class="tagline">Prosthetic &amp; Orthotic Services</div>

  <div class="person-name">Marlo Venteski</div>
  <div class="person-title">Orthotist/Prosthetist</div>

  <ul class="contact-list contact-list--office">
    <li><svg viewBox="0 0 12 12"><path d="M1 4c0-2 2-3 5-3s5 1 5 3l-2 1-1-1.5H4L3 5 1 4zM2.5 6h7l1 5h-9z"/></svg>718.555.0142</li>
    <li><svg viewBox="0 0 12 12"><path d="M3 1h6v3H3zM1 5h10v4H9v2H3V9H1zM4 8v2h4V8z"/></svg>718.555.0187</li>
    <li><svg viewBox="0 0 12 12"><path d="M6 1a5 5 0 1 0 0 10A5 5 0 0 0 6 1zm0 1.2c.6.6 1 1.6 1.1 3.2H4.9C5 3.8 5.4 2.8 6 2.2zM4.9 6.6h2.2C7 8.2 6.6 9.2 6 9.8c-.6-.6-1-1.6-1.1-3.2zM2.3 5.4A3.8 3.8 0 0 1 4.3 2.6c-.3.8-.5 1.7-.6 2.8zm0 1.2h1.4c.1 1.1.3 2 .6 2.8a3.8 3.8 0 0 1-2-2.8zm5.4 2.8c.3-.8.5-1.7.6-2.8h1.4a3.8 3.8 0 0 1-2 2.8zm.6-4c-.1-1.1-.3-2-.6-2.8a3.8 3.8 0 0 1 2 2.8z"/></svg>www.kinetralimb.com</li>
    <li class="address">2210 Harbor Ave. Brooklyn, NY 11235</li>
  </ul>

  <ul class="contact-list contact-list--personal">
    <li><svg viewBox="0 0 12 12"><path d="M3 0h6a1 1 0 0 1 1 1v10a1 1 0 0 1-1 1H3a1 1 0 0 1-1-1V1a1 1 0 0 1 1-1zm.5 1.5v8h5v-8zM6 10.2a.6.6 0 1 0 0 1.2.6.6 0 0 0 0-1.2z"/></svg>845-555-0163</li>
    <li><svg viewBox="0 0 12 12"><path d="M0 2.5h12v1L6 7 0 3.5zM0 4.8l6 3.5 6-3.5V10H0z"/></svg>mventeski@kinetralimb.com</li>
  </ul>

  <div class="footer-band"></div>
</section>

</body>
</html>
```